Full re-design of visual identity

We have just re-designed our logo and would like to apply it on our folders, business cards, stationery, and etc... we are attaching new logo + the material we need to re-design... we will provide full corel draw files to help make job easier and also because lot of icons and artwork can be still used...

any doubts we are at your disposal. thanks in advance.

```html
<!DOCTYPE html>
<html lang="en">
<head>
<meta charset="utf-8">
<title>Lumora Stationery Set</title>
<link href="https://fonts.googleapis.com/css2?family=Open+Sans:wght@400;600;700&display=swap" rel="stylesheet">
<style>
  :root{
    --orange:#ee8a55;
    --orange-deep:#e9762f;
    --paper:#ffffff;
    --ink:#5a5a5a;
    --ink-soft:#8d8d8d;
    --line:#9a9a9a;
    --bg:#ececec;
  }
  *{box-sizing:border-box;margin:0;padding:0}
  html,body{width:1200px;height:1000px;overflow:hidden}
  body{background:var(--bg);font-family:"Open Sans",Arial,sans-serif;color:var(--ink);position:relative}
  .sheet{position:absolute;box-shadow:0 2px 6px rgba(0,0,0,.12)}
  .brand{font-weight:700;letter-spacing:-.5px;display:inline-flex;align-items:center;gap:6px;line-height:1}
  .brand-dot{display:inline-block;border-radius:50%;background:currentColor}
  .brand--light{color:var(--paper)}
  .brand--dark{color:var(--orange-deep)}

  /* business card front */
  .card-front{left:60px;top:90px;width:240px;height:140px;background:var(--orange);display:flex;align-items:center;justify-content:center}
  .card-front .brand{font-size:34px}
  .card-front .brand-dot{width:12px;height:12px}

  /* business card back */
  .card-back{left:330px;top:90px;width:240px;height:140px;background:var(--paper);padding:26px 16px 0 18px}
  .card-back .holder{position:absolute;left:18px;top:44px}
  .card-back .holder-name{font-size:15px;font-weight:600;color:var(--ink)}
  .card-back .holder-title{font-size:7px;color:var(--orange-deep);margin-top:2px}
  .card-back .divider{position:absolute;left:118px;top:34px;width:1px;height:54px;background:var(--line)}
  .card-back .brand{position:absolute;right:14px;top:22px;font-size:13px}
  .card-back .brand-dot{width:5px;height:5px}
  .card-back .contacts{position:absolute;left:128px;top:44px;list-style:none;font-size:6px;color:var(--ink-soft)}
  .card-back .contacts li{display:flex;align-items:center;gap:4px;margin-bottom:3px}
  .card-back .contacts svg{width:6px;height:6px;fill:var(--orange-deep)}
  .card-back .band{position:absolute;left:0;right:0;bottom:14px;height:4px;background:var(--orange-deep)}

  /* folder */
  .folder{left:60px;top:260px;width:510px;height:300px;background:var(--orange);padding:58px 0 0 52px}
  .folder .brand{font-size:46px}
  .folder .brand-dot{width:16px;height:16px}

  /* envelope */
  .envelope{left:60px;top:590px;width:510px;height:260px;background:var(--orange);overflow:hidden}
  .envelope .curve{position:absolute;inset:0}
  .envelope .sender{position:absolute;left:34px;top:34px;list-style:none;font-size:7px;color:var(--paper)}
  .envelope .sender li{display:flex;align-items:center;gap:5px;margin-bottom:4px}
  .envelope .sender svg{width:7px;height:7px;fill:var(--paper)}
  .envelope .brand{position:absolute;right:26px;bottom:22px;font-size:28px}
  .envelope .brand-dot{width:10px;height:10px}

  /* letterhead */
  .letterhead{left:640px;top:90px;width:500px;height:707px;background:var(--paper)}
  .letterhead .brand{position:absolute;right:46px;top:52px;font-size:40px}
  .letterhead .brand-dot{width:14px;height:14px}
  .meta{position:absolute;left:46px;top:70px;font-size:8px;line-height:1.25}
  .meta dt{color:var(--orange-deep);font-weight:700;text-transform:uppercase}
  .meta dd{color:var(--ink-soft);margin-bottom:4px}
  .rule{position:absolute;left:46px;right:46px;height:1px;background:var(--line)}
  .letter-title{position:absolute;left:46px;right:46px;top:150px;text-align:center;color:var(--orange-deep);font-size:13px;font-weight:700}
  .letter-body{position:absolute;left:46px;right:46px;top:196px;font-size:8.5px;line-height:1.55;color:var(--ink-soft)}
  .letter-body p{margin-bottom:12px}
  .signature{position:absolute;right:60px;top:470px;width:150px;height:44px;background:linear-gradient(90deg,#f4f4f4,#e6e6e6);border-radius:4px}
  .letter-contacts{position:absolute;right:80px;top:548px;list-style:none;font-size:8px;color:var(--ink-soft)}
  .letter-contacts li{display:flex;align-items:center;gap:6px;margin-bottom:4px}
  .letter-contacts svg{width:8px;height:8px;fill:var(--orange-deep)}
  .letter-band{position:absolute;left:0;right:0;bottom:20px;height:6px;background:var(--orange-deep)}
</style>
</head>
<body>

<svg width="0" height="0" style="position:absolute">
  <defs>
    <symbol id="icon-pin" viewBox="0 0 10 10"><path d="M5 0a3.5 3.5 0 0 0-3.5 3.5C1.5 6 5 10 5 10s3.5-4 3.5-6.5A3.5 3.5 0 0 0 5 0zm0 5a1.5 1.5 0 1 1 0-3 1.5 1.5 0 0 1 0 3z"/></symbol>
    <symbol id="icon-phone" viewBox="0 0 10 10"><path d="M2 0h2l1 2.5-1.3 1a6 6 0 0 0 2.8 2.8l1-1.3L10 6v2a2 2 0 0 1-2 2A8 8 0 0 1 0 2a2 2 0 0 1 2-2z"/></symbol>
    <symbol id="icon-mail" viewBox="0 0 10 10"><path d="M0 2h10v6H0zM0 2l5 3.5L10 2" /><path d="M0 2.6l5 3.5 5-3.5V2L5 5.4 0 2z" fill="#fff"/></symbol>
    <symbol id="icon-web" viewBox="0 0 10 10"><circle cx="5" cy="5" r="5"/><path d="M0 5h10M5 0c-2 2.5-2 7.5 0 10M5 0c2 2.5 2 7.5 0 10" stroke="#fff" stroke-width=".7" fill="none"/></symbol>
  </defs>
</svg>

<section class="sheet card-front" aria-label="Business card front">
  <span class="brand brand--light">Lumora<span class="brand-dot"></span></span>
</section>

<section class="sheet card-back" aria-label="Business card back">
  <div class="holder">
    <p class="holder-name">Daniel Reyes</p>
    <p class="holder-title">Chief Executive Officer</p>
  </div>
  <span class="divider"></span>
  <span class="brand brand--dark">Lumora<span class="brand-dot"></span></span>
  <ul class="contacts">
    <li><svg><use href="#icon-pin"/></svg>48 Harbor Lane, Westfield</li>
    <li><svg><use href="#icon-phone"/></svg>555-0148-22</li>
    <li><svg><use href="#icon-mail"/></svg>hello@lumora.net</li>
    <li><svg><use href="#icon-web"/></svg>www.lumora.net</li>
  </ul>
  <span class="band"></span>
</section>

<section class="sheet folder" aria-label="Presentation folder">
  <span class="brand brand--light">Lumora<span class="brand-dot"></span></span>
</section>

<section class="sheet envelope" aria-label="Envelope">
  <svg class="curve" viewBox="0 0 510 260" preserveAspectRatio="none">
    <path d="M0 190 Q 300 200 510 130 L510 260 L0 260 Z" fill="#ffffff"/>
  </svg>
  <ul class="sender">
    <li><svg><use href="#icon-pin"/></svg>48 Harbor Lane, Westfield, 20410</li>
    <li><svg><use href="#icon-phone"/></svg>555-0148-22</li>
    <li><svg><use href="#icon-mail"/></svg>hello@lumora.net</li>
    <li><svg><use href="#icon-web"/></svg>www.lumora.net</li>
  </ul>
  <span class="brand brand--dark">Lumora<span class="brand-dot"></span></span>
</section>

<section class="sheet letterhead" aria-label="Letterhead">
  <span class="brand brand--dark">Lumora<span class="brand-dot"></span></span>
  <dl class="meta">
    <dt>Subject</dt><dd>Quarterly update</dd>
    <dt>Date</dt><dd>07-05-2024</dd>
    <dt>Addressed to</dt><dd>Client Relations</dd>
  </dl>
  <p class="letter-title">Lorem ipsum dolor sit ametconsectetur.</p>
  <span class="rule" style="top:176px"></span>
  <div class="letter-body">
    <p>Thank you for choosing our network services. This letter confirms the upgrade of your connection plan, which will take effect next month. Our team will contact you to arrange a short visit and ensure every device stays online during the change.</p>
    <p>Should you have any questions about billing, speeds or equipment, please reply to this letter or call our support line. We look forward to serving you for many years and thank you for your continued trust.</p>
    <p>Best regards,</p>
  </div>
  <span class="rule" style="top:430px"></span>
  <div class="signature" role="img" aria-label="Handwritten signature of Daniel Reyes"></div>
  <span class="rule" style="top:530px;left:250px"></span>
  <ul class="letter-contacts">
    <li><svg><use href="#icon-pin"/></svg>48 Harbor Lane, Westfield, 20410</li>
    <li><svg><use href="#icon-phone"/></svg>555-0148-22</li>
    <li><svg><use href="#icon-mail"/></svg>hello@lumora.net</li>
    <li><svg><use href="#icon-web"/></svg>www.lumora.net</li>
  </ul>
  <span class="letter-band"></span>
</section>

</body>
</html>
```